Roll-Up Banner für Glückswebsite
Das war eine großartige Zusammenarbeit und unserem sehr knappen Zeitplan extrem entgegenkommend. Das design ist gleichzeitig seriös und trotzdem jung und dynamisch! Perfekt!
Zielgruppe
Die Website, www.freudenkompass.de ermöglicht es jedem Interessierten kostenlos mehr über das eigene Lebensglück, persönliche Stärken, und die eigene Lebenszufriedenheit herauszufinden. Interessierte können online Fragebögen ausfüllen, und erhalten neben einer detaillierten Rückmeldung über die eigenen Möglichkeiten und Stärken, Hinweise dazu, wie Sie an Ihrem eigenen Potenzial arbeiten können. Es handelt sich um ein Kooperationsprojekt der Nordischen Vereinigung für Heitere Seelenkunde der Uni Kellbrunn, der TH-Marwald, der Health Academy Ostrau und der Uni Felsheim. Zielgruppe für das Banner sind Menschen, die selbst mit Klienten im Kontext der Positiven Psychologie arbeiten oder Menschen, die sich Ihrem eigenen Lebensglück zuwenden wollen.
Aufgabenstellung
Es handelt sich um ein Roll-up Banner in den Maßen 1m Breite und 2 Meter Höhe.
Das Banner sollte so angelegt sein, dass es interessierten Besuchern auf Kongressen vermittelt, was es mit der Seite Freudenkompass.de auf sich hat. Also wissenschaftlich evaluierte kostenfreie online-Fragebögen, die Menschen dabei helfen Ihre eigenen Stärken und Potenziale zu entdecken und dem eigenen Glück näher zu kommen.
Es sollte außerdem das Logo der NVHS darauf zu sehen sein, sowie kleiner die Logos der Forschungskooperationspartner, TH-Marwald, Uni Kellbrunn, Uni Felsheim, Health Academy Ostrau.
Die Farben sollten zum Logo der NVHS passen.

```html
<!DOCTYPE html>
<html lang="de">
<head>
<meta charset="utf-8">
<title>Freudenkompass – Roll-Up</title>
<link rel="stylesheet" href="https://fonts.googleapis.com/css2?family=Fira+Sans:wght@300;400;500;600&display=swap">
<style>
  :root{
    --bg:#9aa1ac;
    --green:#6ab862;
    --teal:#2aa3b8;
    --teal-deep:#2f9a98;
    --green-deep:#5ea85a;
    --navy:#1b3a6b;
    --navy-dark:#0c2a5c;
    --white:#ffffff;
    --paper:#f4f5f7;
    --footer:#e4e6ea;
    --dot-1:#72c3d6;
    --dot-2:#24998f;
    --dot-3:#2b9a5e;
    --dot-4:#1f3d73;
  }
  *{margin:0;padding:0;box-sizing:border-box}
  html,body{width:768px;height:1200px;overflow:hidden;background:var(--bg);font-family:"Fira Sans",sans-serif}
  .banner{position:absolute;left:78px;top:0;width:612px;height:1200px;background:var(--paper);overflow:hidden}
  .url-band{position:absolute;left:0;top:0;width:100%;height:125px;
    background:linear-gradient(90deg,var(--green) 0%,#4fb0a0 55%,var(--teal) 100%)}
  .url-band h1{position:absolute;left:44px;top:48px;font-size:47px;font-weight:600;color:var(--white);letter-spacing:-1.2px;line-height:1}
  .hero{position:absolute;left:0;top:125px;width:100%;height:328px;background:var(--paper)}
  .hero-photo{position:absolute;left:0;top:0;width:360px;height:328px;
    background:linear-gradient(90deg,#b99575 0%,#c9a98c 35%,#d9cfc6 70%,rgba(244,245,247,0) 100%)}
  .society{position:absolute;left:414px;top:28px;width:180px}
  .society-mark{display:flex;align-items:center;gap:10px;margin-left:22px}
  .society-mark .dot{width:44px;height:44px;border-radius:50%;background:var(--teal-deep)}
  .society-name{font-size:22px;font-weight:600;color:var(--navy);letter-spacing:2px;margin-top:10px;margin-left:22px}
  .society-full{font-size:9.5px;font-weight:400;color:var(--navy);line-height:1.3;margin-left:22px;margin-top:4px}
  .headline{position:absolute;right:46px;top:195px;text-align:right;font-size:38px;font-weight:600;color:var(--navy);line-height:1.27;letter-spacing:-0.6px}
  .info{position:absolute;left:0;top:453px;width:100%;height:592px;
    background:linear-gradient(160deg,#5db59a 0%,var(--teal) 35%,var(--teal-deep) 70%,var(--green-deep) 100%)}
  .info::after{content:"";position:absolute;inset:0;background:linear-gradient(30deg,rgba(106,184,98,.75) 0%,rgba(106,184,98,0) 50%)}
  .intro{position:absolute;left:45px;top:35px;width:520px;font-size:18px;font-weight:300;color:var(--white);line-height:23.5px;z-index:1}
  .steps{position:absolute;left:45px;top:174px;z-index:1;width:560px}
  .steps .rail{position:absolute;left:14px;top:14px;width:1.5px;height:236px;background:rgba(255,255,255,.8)}
  .step{position:absolute;left:0;display:flex}
  .step .dot{width:29px;height:29px;border-radius:50%;border:2px solid var(--white);flex:none}
  .step .text{margin-left:31px;color:var(--white);font-weight:300}
  .step .title{font-size:24px;line-height:29px}
  .step .sub{font-size:18px;line-height:24px;margin-top:5px}
  .step-1{top:0}.step-1 .dot{background:var(--dot-1)}
  .step-2{top:88px}.step-2 .dot{background:var(--dot-2)}
  .step-3{top:177px}.step-3 .dot{background:var(--dot-3)}
  .step-4{top:236px}.step-4 .dot{background:var(--dot-4)}
  .seal{position:absolute;left:432px;top:251px;width:184px;height:54px;background:var(--navy-dark);transform:rotate(-2deg);z-index:2;
    color:var(--white);font-size:13px;font-weight:400;text-align:center;line-height:17px;padding-top:9px}
  .rule{position:absolute;left:0;top:1045px;width:100%;height:6px;background:var(--navy-dark)}
  .partners{position:absolute;left:0;top:1051px;width:100%;height:149px;background:var(--footer)}
  .partners h2{position:absolute;left:45px;top:22px;font-size:18.5px;font-weight:400;color:var(--navy)}
  .partner-list{position:absolute;left:45px;top:72px;width:530px;display:flex;justify-content:space-between;align-items:center}
  .partner{display:flex;align-items:center;gap:5px;font-size:10.5px;font-weight:400;color:var(--navy);line-height:1.2}
  .partner .mark{width:22px;height:22px;border-radius:50%;background:#8f97a6;flex:none}
</style>
</head>
<body>
<main class="banner">
  <header class="url-band"><h1>www.freudenkompass.de</h1></header>

  <section class="hero">
    <div class="hero-photo" role="img" aria-label="Foto: lächelnder junger Mann mit Brille in einem hellen Raum"></div>
    <div class="society">
      <div class="society-mark"><span class="dot"></span></div>
      <div class="society-name">NVHS</div>
      <div class="society-full">Nordische Vereinigung für<br>Heitere Seelenkunde</div>
    </div>
    <h2 class="headline">Kennen Sie sich<br>und Ihre Stärken?</h2>
  </section>

  <section class="info">
    <p class="intro">Unter www.freudenkompass.de haben Sie die Möglichkeit kostenfrei die neusten wissenschaftlichen Fragebögen im Bereich der Positiven Psychologie zu nutzen und ein detail­liertes Feedback zu Ihren Ergebnissen zu erhalten.</p>
    <div class="steps">
      <span class="rail"></span>
      <div class="step step-1"><span class="dot"></span><div class="text"><div class="title">Registrieren</div><div class="sub">– und damit immer Zugriff auf Ihre Ergebnisse haben</div></div></div>
      <div class="step step-2"><span class="dot"></span><div class="text"><div class="title">Online-Fragebogen ausfüllen</div><div class="sub">unter www.freudenkompass.de</div></div></div>
      <div class="step step-3"><span class="dot"></span><div class="text"><div class="title">Persönliche Rückmeldung erhalten</div></div></div>
      <div class="step step-4"><span class="dot"></span><div class="text"><div class="title">Ein noch erfüllteres Leben gestalten</div></div></div>
    </div>
    <div class="seal">wissenschaftlich evaluiert<br>kostenfrei | anonym</div>
  </section>

  <div class="rule"></div>

  <footer class="partners">
    <h2>Forschungskooperationspartner</h2>
    <div class="partner-list">
      <div class="partner"><span class="mark"></span>Uni<br>Kellbrunn</div>
      <div class="partner"><span class="mark"></span>Health Academy<br>Ostrau</div>
      <div class="partner"><span class="mark"></span>TH-Marwald</div>
      <div class="partner"><span class="mark"></span>Uni<br>Felsheim</div>
    </div>
  </footer>
</main>
</body>
</html>
```